Website Design for Videographer

I am looking to update my website - www.brinolvaske.com. I am a wedding videographer who specialises in natural and documentary videography.

The website will be built by my designer using the Wordpress Plinthworx framework.

Requirements;
I want the website to have a clean white look mixed in with video footage.
Needs to be classy. At the moment my website uses a lot of Gold. On the new look I DO NOT want gold.

Need a web and mobile design for the following 12 pages;

* Home page (need to have example videos and text)
* About (this is about me and my service)
* Videos (examples of my work)
* Testimonials
* Packages
* Contact
* Content (this is to show social media content that I am making in a vertical format and advertise this service).
* Blog (index page for blog)
* Blog pages (individual pages for blog content)
* Wedding Venues Index Page (https://brinolvaske.com/north-east-wedding-venues/)
* Individual venue pages (https://brinolvaske.com/north-east-wedding-venues/marlow-tendle-lodge-wedding-videos/) - Needs to show videos, photos, text as is on the current page.
* Venue Tours (https://brinolvaske.com/wedding-venue-tours/)

My current logo is attached however on the website I want to go for a black and white style for it.

Example styles I like however must not be copied.
https://joswelbrant.co.uk/about/
https://oakandripple.co.uk/ (if done in white)
https://tumblemothpictures.co.uk/

Target Market(s)

Couples getting married aged 25-35

Industry/Entity Type

Weddings

Number of Pages Required

5+ page

Font styles to use
Sans Serif

Requirements
Must have
• A classy look, black and white, use videos and photos.
Should not have
• Gold colour

```html
<!DOCTYPE html>
<html lang="en">
<head>
<meta charset="utf-8">
<title>Brin Olvaske Wedding Films — Mobile Preview</title>
<link rel="stylesheet" href="https://fonts.googleapis.com/css2?family=Jost:wght@300;400;500&display=swap">
<style>
  :root{
    --ink:#0b0b0b;
    --paper:#ffffff;
    --frame:#b9b6b7;
    --shadow-box:#eeeeee;
    --muted:#3a3a3a;
    --rule:#6d6d6d;
    --white:#ffffff;
    --dark-top:#2b2b2b;
    --dark-mid:#3a3a3a;
    --dark-end:#1b1b1b;
  }
  *{margin:0;padding:0;box-sizing:border-box}
  html,body{width:1200px;height:702px;overflow:hidden;background:var(--paper)}
  .stage{position:relative;width:1200px;height:702px;overflow:hidden;background:var(--paper);
    font-family:"Jost",sans-serif;color:var(--ink)}
  .abs{position:absolute}
  .center{left:0;width:100%;text-align:center}

  /* intro panel */
  .intro{position:absolute;left:0;top:206px;width:143px;height:249px;background:var(--ink);color:var(--white);text-align:center}
  .intro .brand{position:absolute;left:0;width:100%;top:82px;font-weight:500;font-size:10.5px;letter-spacing:2.5px}
  .intro .kicker{position:absolute;left:0;width:100%;top:141px;font-weight:400;font-size:10.5px;letter-spacing:.3px}
  .intro .big{position:absolute;left:0;width:100%;top:158px;font-weight:400;font-size:22px;letter-spacing:.8px}

  /* screens */
  .col{position:absolute;top:0;width:155px;height:702px}
  .frame{position:absolute;left:0;width:155px;background:var(--paper);border-left:5px solid var(--frame);border-right:5px solid var(--frame)}
  .frame.top-round{border-top:5px solid var(--frame);border-radius:22px 22px 0 0}
  .frame.bottom-round{border-bottom:5px solid var(--frame);border-radius:0 0 22px 22px}

  .photo{position:absolute}
  .eyebrow{position:absolute;font-weight:400;font-size:7.5px;letter-spacing:.5px}
  .eyebrow .dash{display:inline-block;width:12px;border-top:.7px solid var(--ink);vertical-align:middle;margin:0 3px}
  .title{position:absolute;font-weight:400;font-size:10.5px;line-height:16px;letter-spacing:.5px}
  .body{position:absolute;font-weight:300;font-size:4.4px;line-height:7px;color:var(--muted)}
  .btn{position:absolute;height:21px;line-height:21px;text-align:center;font-size:5.6px;letter-spacing:.5px;border-radius:2px}
  .btn.solid{background:var(--ink);color:var(--white)}
  .btn.outline{border:.8px solid var(--ink);color:var(--ink);background:var(--paper)}
  .btn svg{vertical-align:middle;margin-left:4px}
  .section-rule{position:absolute;left:5px;width:145px;height:10px}
  .section-rule::before,.section-rule::after{content:"";position:absolute;top:5px;width:32px;border-top:.7px solid var(--rule)}
  .section-rule::before{left:0}.section-rule::after{right:0}
  .section-rule span{position:absolute;left:0;width:100%;text-align:center;font-weight:400;font-size:7.5px;line-height:10px;letter-spacing:.4px}

  .card-title{position:absolute;font-weight:500;font-size:6.8px;letter-spacing:.2px}
  .card-date{position:absolute;font-size:3.5px;color:#777}
  .round-arrow{position:absolute;width:12px;height:12px}

  /* dark sections */
  .dark{position:absolute;left:5px;width:145px;background:linear-gradient(180deg,var(--dark-top),var(--dark-mid) 45%,var(--dark-end));color:var(--white)}
  .quote-card{position:absolute;border:.8px solid rgba(255,255,255,.85);border-radius:4px}
  .quote{position:absolute;text-align:center;font-weight:300;font-size:6.3px;line-height:10px;color:var(--white)}
  .avatar{position:absolute;width:22px;height:22px;border-radius:50%;background:#b9b3b0;border:1px solid #fff}
  .client-name{position:absolute;font-size:7.5px;color:var(--white)}
  .client-role{position:absolute;font-size:3.8px;color:#ddd}

  .footer{position:absolute;left:5px;width:145px;background:var(--ink);color:var(--white)}
  .footer .brand{position:absolute;left:0;width:100%;text-align:center;font-weight:500;font-size:6.5px;letter-spacing:1.8px}
  .footer .label{position:absolute;font-size:4.8px;letter-spacing:.4px}
  .footer .item{position:absolute;font-weight:300;font-size:4.4px;letter-spacing:.3px}
  .social{position:absolute;width:8px;height:8px;border:.8px solid var(--white);border-radius:50%}
  .nl-input{position:absolute;height:11px;background:var(--white)}
  .nl-send{position:absolute;height:11px;line-height:11px;background:var(--white);color:var(--ink);font-size:5px;text-align:center}
</style>
</head>
<body>
<div class="stage">

  <!-- intro panel -->
  <div class="intro">
    <div class="brand">BRIN OLVASKE</div>
    <div class="kicker">PREVIEW MOBILE</div>
    <div class="big">VERSION</div>
  </div>

  <!-- screen 1: hero + about -->
  <div class="col" style="left:168px">
    <div class="frame top-round" style="top:77px;height:640px"></div>
    <div class="photo" role="img" aria-label="Couple walking hand in hand through a meadow at sunset"
      style="left:6px;top:83px;width:143px;height:327px;border-radius:16px 16px 0 0;background:linear-gradient(160deg,#8f8c8a 0%,#5e554f 35%,#2f2b29 65%,#6d645e 100%)"></div>
    <div class="abs" style="left:14px;top:103px;font-weight:500;font-size:4.8px;letter-spacing:1px;color:#fff">BRIN OLVASKE</div>
    <svg class="abs" style="left:124px;top:101px" width="11" height="9" viewBox="0 0 11 9"><path d="M0 1h11M0 4.5h11M0 8h11" stroke="#fff" stroke-width="1"/></svg>
    <div class="abs" style="left:30px;top:126px;width:96px;border-top:.6px solid rgba(255,255,255,.8)"></div>
    <div class="abs center" style="top:189px;font-size:6.8px;letter-spacing:.3px;color:#fff">WELCOME TO DREAM</div>
    <div class="abs center" style="top:199px;font-size:10.8px;line-height:16px;letter-spacing:.4px;color:#fff">PLAN THE PERFECT<br>WEDDING</div>
    <div class="abs center" style="top:257px;padding:0 20px;font-weight:300;font-size:4.3px;line-height:7px;color:#fff">Capture every moment on your wedding day so that it will become the most beautiful memory that cannot be forgotten later in the future.</div>
    <div class="abs" style="left:30px;top:392px;width:96px;border-top:.6px solid rgba(255,255,255,.8)"></div>

    <div class="eyebrow center" style="top:471px"><span class="dash"></span>MEET BRIN<span class="dash"></span></div>
    <div class="title center" style="top:484px">CAPTURE EVERY<br>MOMENT</div>
    <div class="body center" style="top:542px;padding:0 20px">With 25 years of video production and media industry experience, incredible testimonials, a calm persona, and the ability to blend into the background when necessary, you can rest assured you're in safe hands.<br>I am a Durham Wedding Videographer and live in a little village in County Durham overlooking the countryside and I am available to shoot all over the North East and UK. In the last few years, I've filmed in the USA, Italy, Greece, France, Portugal and Spain to name a few countries.</div>
    <div class="btn solid" style="left:46px;top:651px;width:61px">CONTACT</div>
    <div class="btn outline" style="left:46px;top:699px;width:61px"></div>
  </div>

  <!-- screen 2: about + films -->
  <div class="col" style="left:343px">
    <div class="frame" style="top:0;height:702px"></div>
    <div class="eyebrow center" style="top:26px"><span class="dash"></span>MEET BRIN<span class="dash"></span></div>
    <div class="title center" style="top:39px">CAPTURE EVERY<br>MOMENT</div>
    <div class="body center" style="top:97px;padding:0 18px">With 25 years of video production and media industry experience, incredible testimonials, a calm persona, and the ability to blend into the background when necessary, you can rest assured you're in safe hands.<br>I am a Durham Wedding Videographer and live in a little village in County Durham overlooking the countryside and I am available to shoot all over the North East and UK. In the last few years, I've filmed in the USA, Italy, Greece, France, Portugal and Spain to name a few countries.</div>
    <div class="btn solid" style="left:43px;top:210px;width:61px">CONTACT</div>
    <div class="btn outline" style="left:43px;top:257px;width:61px">FOLLOW ME</div>
    <div class="abs" style="left:44px;top:349px;width:106px;height:158px;background:var(--shadow-box)"></div>
    <div class="photo" role="img" aria-label="Videographer operating a camera on a slider in a studio"
      style="left:20px;top:333px;width:109px;height:160px;background:linear-gradient(135deg,#2a2a2a 0%,#5a5a5a 40%,#b5b2ae 70%,#8a7766 100%)"></div>
    <div class="section-rule" style="top:552px"><span>WEDDING FILMS</span></div>
    <div class="title center" style="top:600px">RESULTS OF MY<br>WORK</div>
    <div class="body center" style="top:658px;padding:0 18px">Here are the results of the work I have done so far, I always try to provide the best video.</div>
  </div>

  <!-- screen 3: gallery + team -->
  <div class="col" style="left:513px">
    <div class="frame" style="top:0;height:702px"></div>
    <div class="photo" role="img" aria-label="Couple holding hands with bouquet" style="left:20px;top:31px;width:54px;height:38px;background:linear-gradient(135deg,#4f3d34,#a88672)"></div>
    <div class="photo" role="img" aria-label="Bride and groom under a floral arch" style="left:78px;top:31px;width:56px;height:38px;background:linear-gradient(135deg,#6b3e2e,#c2aa98,#4d3026)"></div>
    <div class="photo" role="img" aria-label="Groom kissing bride beneath her veil" style="left:20px;top:72px;width:114px;height:67px;background:linear-gradient(120deg,#e8e6e6,#cfcaca 55%,#2b2b2b)"></div>
    <div class="photo" role="img" aria-label="Smiling bride and groom close together" style="left:20px;top:155px;width:114px;height:66px;background:linear-gradient(120deg,#7d685a,#d5c8bc 50%,#98a08c)"></div>
    <div class="photo" role="img" aria-label="Couple walking out of a stone venue" style="left:21px;top:224px;width:54px;height:38px;background:linear-gradient(135deg,#3a2f2a,#857a72)"></div>
    <div class="photo" role="img" aria-label="Couple walking across a garden lawn" style="left:81px;top:224px;width:53px;height:38px;background:linear-gradient(135deg,#3d4a2c,#7d8b5e,#cfd0cc)"></div>
    <div class="btn outline" style="left:45px;top:307px;width:66px">VIEW ALL<svg width="11" height="6" viewBox="0 0 11 6"><path d="M0 3h10M7.5 .5 10 3 7.5 5.5" fill="none" stroke="#0b0b0b" stroke-width=".8"/></svg></div>
    <div class="abs" style="left:30px;top:368px;width:96px;border-top:.7px solid var(--rule)"></div>
    <div class="eyebrow center" style="top:416px"><span class="dash"></span>OUR TEAM<span class="dash"></span></div>
    <div class="title center" style="top:435px">OUR CREATIVE<br>TEAM</div>
    <div class="body center" style="top:494px;padding:0 18px">Our team members have experience working with a diverse range of clients, from startups to large corporations, successfully implementing effective creative strategies. We believe that collaboration is the key to generating brilliant ideas. Each team member supports and contributes to one another, ensuring that every project not only meets but also exceeds client expectations.</div>
    <div class="btn solid" style="left:51px;top:584px;width:54px">CONTACT</div>
    <div class="btn outline" style="left:51px;top:631px;width:54px">EXPLORE</div>
    <div class="photo" role="img" aria-label="Film crew on location" style="left:14px;top:688px;width:123px;height:14px;background:linear-gradient(90deg,#2e2e2e,#6a6a6a,#2e2e2e)"></div>
  </div>

  <!-- screen 4: crew + blog -->
  <div class="col" style="left:684px">
    <div class="frame" style="top:0;height:702px"></div>
    <div class="abs" style="left:6px;top:29px;width:112px;height:82px;background:var(--shadow-box)"></div>
    <div class="photo" role="img" aria-label="Film crew with cameras on a street shoot" style="left:14px;top:22px;width:123px;height:78px;background:linear-gradient(135deg,#5a5a5a,#9c9c9c 45%,#2c2c2c)"></div>
    <div class="section-rule" style="top:178px"><span>OUR BLOG</span></div>
    <div class="body center" style="top:227px;padding:0 20px">Welcome to our blog! Here, we share insights, tips, and inspiration from the creative world. From marketing strategies to innovative design, we hope our content adds value and helps you explore your creative potential.</div>
    <div class="photo" role="img" aria-label="Reception table with pink flowers and string lights" style="left:30px;top:306px;width:100px;height:69px;background:linear-gradient(135deg,#6a6257,#e7a9bd 50%,#7d7166)"></div>
    <div class="card-title" style="left:30px;top:381px">BEST DECORATION</div>
    <div class="card-date" style="left:30px;top:392px">Wednesday | July-14-2024</div>
    <div class="body center" style="top:401px;padding:0 22px;font-size:4.2px;line-height:6.6px">We believe that collaboration is the key to generating brilliant ideas. Each team member supports and contributes to one another, ensuring that every project not only meets but also exceeds client expectations.</div>
    <svg class="round-arrow" style="left:68px;top:442px" viewBox="0 0 12 12"><circle cx="6" cy="6" r="5.5" fill="none" stroke="#0b0b0b" stroke-width=".6"/><path d="M3.5 6h5M6.8 4.3 8.5 6 6.8 7.7" fill="none" stroke="#0b0b0b" stroke-width=".6"/></svg>
    <div class="photo" role="img" aria-label="White table setting with roses" style="left:30px;top:481px;width:100px;height:69px;background:linear-gradient(135deg,#b9a3cf,#f0eef2 50%,#d86a86)"></div>
    <div class="card-title" style="left:30px;top:557px">BEST THEME</div>
    <div class="card-date" style="left:30px;top:568px">Wednesday | July-14-2024</div>
    <div class="body center" style="top:577px;padding:0 22px;font-size:4.2px;line-height:6.6px">We believe that collaboration is the key to generating brilliant ideas. Each team member supports and contributes to one another, ensuring that every project not only meets but also exceeds client expectations.</div>
    <svg class="round-arrow" style="left:71px;top:617px" viewBox="0 0 12 12"><circle cx="6" cy="6" r="5.5" fill="none" stroke="#0b0b0b" stroke-width=".6"/><path d="M3.5 6h5M6.8 4.3 8.5 6 6.8 7.7" fill="none" stroke="#0b0b0b" stroke-width=".6"/></svg>
    <div class="btn outline" style="left:41px;top:675px;width:66px">VIEW ALL<svg width="11" height="6" viewBox="0 0 11 6"><path d="M0 3h10M7.5 .5 10 3 7.5 5.5" fill="none" stroke="#0b0b0b" stroke-width=".8"/></svg></div>
  </div>

  <!-- screen 5: testimonials + footer -->
  <div class="col" style="left:855px">
    <div class="frame" style="top:0;height:702px"></div>
    <div class="btn outline" style="left:41px;top:-7px;width:66px">VIEW ALL<svg width="11" height="6" viewBox="0 0 11 6"><path d="M0 3h10M7.5 .5 10 3 7.5 5.5" fill="none" stroke="#0b0b0b" stroke-width=".8"/></svg></div>
    <div class="dark" role="img" aria-label="Wedding guests celebrating at an evening reception" style="top:61px;height:365px"></div>
    <div class="abs center" style="top:96px;font-size:10.5px;color:#fff;letter-spacing:.6px">WHAT CLIENT SAY</div>
    <div class="abs center" style="top:130px;font-weight:300;font-size:6.2px;color:#fff">Their response after using our services</div>
    <div class="quote-card" style="left:15px;top:179px;width:124px;height:208px"></div>
    <div class="quote" style="left:34px;top:195px;width:86px">“ Their creativity in putting together the video was impressive, and the final product exceeded our expectations. Every detail, from facial expressions to candid moments, was beautifully captured. Additionally, they were very responsive to our requests and ideas.”</div>
    <div class="avatar" style="left:31px;top:342px"></div>
    <div class="client-name" style="left:58px;top:344px">Tobias Renwick</div>
    <div class="client-role" style="left:58px;top:356px">CEO Halden Studio</div>

    <div class="footer" style="top:471px;height:231px">
      <div class="brand" style="top:56px">BRIN OLVASKE</div>
      <div class="label" style="left:0;width:100%;text-align:center;top:92px">FOLLOW US :</div>
      <div class="social" style="left:35px;top:112px"></div>
      <div class="social" style="left:57px;top:112px"></div>
      <div class="social" style="left:78px;top:112px"></div>
      <div class="social" style="left:98px;top:112px"></div>
      <div class="label" style="left:21px;top:146px">NAVIGATION</div>
      <div class="item" style="left:21px;top:163px">ABOUT BRIN</div>
      <div class="item" style="left:21px;top:175px">WEDDING FILMS</div>
      <div class="item" style="left:21px;top:187px">TESTIMONIALS</div>
      <div class="item" style="left:21px;top:198px">PACKAGES</div>
      <div class="item" style="left:21px;top:210px">BLOG</div>
    </div>
  </div>

  <!-- screen 6: testimonial end + full footer -->
  <div class="col" style="left:1026px">
    <div class="frame bottom-round" style="top:0;height:708px"></div>
    <div class="dark" role="img" aria-label="Wedding guests celebrating at an evening reception" style="top:0;height:167px"></div>
    <div class="quote-card" style="left:15px;top:-10px;width:124px;height:138px"></div>
    <div class="quote" style="left:34px;top:-5px;width:86px">detail, from facial expressions to candid moments, was beautifully captured. Additionally, they were very responsive to our requests and ideas.”</div>
    <div class="avatar" style="left:31px;top:83px"></div>
    <div class="client-name" style="left:58px;top:85px">Tobias Renwick</div>
    <div class="client-role" style="left:58px;top:97px">CEO Halden Studio</div>

    <div class="footer" style="top:212px;height:491px;border-radius:0 0 17px 17px">
      <div class="brand" style="top:56px">BRIN OLVASKE</div>
      <div class="label" style="left:0;width:100%;text-align:center;top:92px">FOLLOW US :</div>
      <div class="social" style="left:35px;top:111px"></div>
      <div class="social" style="left:57px;top:111px"></div>
      <div class="social" style="left:78px;top:111px"></div>
      <div class="social" style="left:98px;top:111px"></div>
      <div class="label" style="left:20px;top:147px">NAVIGATION</div>
      <div class="item" style="left:20px;top:163px">ABOUT BRIN</div>
      <div class="item" style="left:20px;top:175px">WEDDING FILMS</div>
      <div class="item" style="left:20px;top:187px">TESTIMONIALS</div>
      <div class="item" style="left:20px;top:198px">PACKAGES</div>
      <div class="item" style="left:20px;top:210px">BLOG</div>
      <div class="label" style="left:20px;top:244px">CONTACT</div>
      <svg class="abs" style="left:20px;top:261px" width="6" height="6" viewBox="0 0 6 6"><path d="M1 .5 2.2 .5 2.7 2 2 2.6C2.4 3.4 2.9 3.9 3.6 4.2L4.1 3.5 5.5 4V5.3C3 5.6 .4 3 1 .5Z" fill="none" stroke="#fff" stroke-width=".5"/></svg>
      <div class="item" style="left:30px;top:261px;font-size:4.2px">07700 900 418</div>
      <svg class="abs" style="left:20px;top:272px" width="7" height="5" viewBox="0 0 7 5"><rect x=".3" y=".3" width="6.4" height="4.4" fill="none" stroke="#fff" stroke-width=".5"/><path d="M.3.3 3.5 2.8 6.7.3" fill="none" stroke="#fff" stroke-width=".5"/></svg>
      <div class="item" style="left:31px;top:271px;font-size:4.2px">films@brinolvaske.com</div>
      <div class="label" style="left:20px;top:307px">NEWSLETTER</div>
      <div class="item" style="left:20px;top:322px;width:106px;font-size:5.4px;line-height:9.5px">Lorem ipsum dolor sit amet, consectetur adipiscing elit. Sed do eiusmod tempor .</div>
      <div class="nl-input" style="left:20px;top:358px;width:67px"></div>
      <div class="nl-send" style="left:89px;top:358px;width:27px">Send</div>
      <div class="abs" style="left:20px;top:421px;width:106px;border-top:.6px solid #777"></div>
      <div class="item" style="left:0;width:100%;text-align:center;top:451px;font-size:3.9px">© 2024 BRIN All Rights Reserved.</div>
    </div>
  </div>

</div>
</body>
</html>
```